Tax Preparation flyer for LedgerVale Corp.

My Client would like a one page PDF flyer to promote upcoming tax season in Canada. This firm is affordable and all virtual. I have attached a copy of their logo and a word document with the proposed wording for the flyer. Please feel free to change if you have better suggestions.

Target Market(s)

individuals in canada

Colors
0054AA
0677BA
7BADD7
CADEEF
E8F1F8

```html
<!DOCTYPE html>
<html lang="en">
<head>
<meta charset="utf-8">
<title>LedgerVale Corp. – Tax Season Flyer</title>
<link rel="stylesheet" href="https://fonts.googleapis.com/css2?family=Poppins:ital,wght@0,400;0,500;0,600;0,700;0,800;1,700&display=swap">
<style>
  :root{
    --blue-deep:#0054AA;
    --blue:#0677BA;
    --blue-bright:#1b9ad6;
    --blue-sky:#4cc2f2;
    --blue-soft:#7BADD7;
    --blue-pale:#CADEEF;
    --blue-mist:#E8F1F8;
    --ink:#222326;
    --charcoal:#2b2c30;
    --grey-panel:#ebebeb;
    --grey-text:#6b6b6b;
    --white:#ffffff;
  }
  *{margin:0;padding:0;box-sizing:border-box}
  html,body{width:783px;height:1200px;overflow:hidden;background:var(--white)}
  body{font-family:"Poppins",sans-serif;color:var(--ink)}
  .flyer{position:relative;width:783px;height:1200px;overflow:hidden;background:var(--white)}
  .abs{position:absolute}

  .hero-art{position:absolute;left:0;top:0}
  .brand{left:54px;top:44px;font-weight:700;font-size:27px;line-height:1;color:var(--blue);letter-spacing:-.5px}
  .headline{left:52px;top:118px}
  .headline .relax{font-weight:800;font-size:70px;line-height:1;letter-spacing:-1px;color:var(--ink)}
  .headline .sub{font-weight:500;font-size:31px;line-height:1;margin-top:8px}
  .headline .covered{font-weight:800;font-size:31px;line-height:1.05;color:var(--blue)}

  .intro{left:55px;top:318px;width:390px;font-size:10.6px;line-height:1.24;color:var(--white)}
  .esign{left:56px;top:397px;font-weight:600;font-size:12px;color:var(--white)}

  .light-band{left:0;top:438px;width:783px;height:206px;background:var(--blue-mist)}
  .portal-icon{left:55px;top:463px;width:22px;height:24px;border-radius:4px;background:var(--blue)}
  .portal-text{left:86px;top:458px;width:280px;font-size:11px;line-height:1.2;color:var(--ink)}
  .discuss{left:56px;top:556px;width:215px;height:62px;border-radius:8px;background:var(--blue);color:var(--white);font-size:11px;line-height:1.2;padding:14px 0 0 40px}
  .discuss svg{position:absolute;left:11px;top:19px}
  .laptop{left:260px;top:542px;width:124px;height:80px}
  .laptop .screen{position:absolute;left:6px;top:0;width:110px;height:72px;border:3px solid var(--ink);background:var(--white);text-align:center;font-size:7.2px;font-weight:600;line-height:1.2;padding-top:8px}
  .laptop .base{position:absolute;left:0;top:72px;width:124px;height:5px;background:#9a9a9a;border-radius:0 0 3px 3px}
  .laptop .dots{display:flex;justify-content:center;gap:4px;margin-top:5px}
  .laptop .dots i{display:block;width:12px;height:12px;border-radius:50%;background:var(--blue)}
  .laptop .dots i+i{background:#5458c9}

  .price{left:414px;top:471px;width:313px;height:152px;border:1.5px solid var(--charcoal);border-radius:12px;overflow:hidden;background:var(--blue-mist)}
  .price .title{position:absolute;left:0;top:-2px;width:100%;text-align:center;font-weight:500;font-size:21px;color:var(--ink)}
  .price .amount{position:absolute;left:0;top:20px;width:100%;text-align:center;font-weight:800;font-size:62px;line-height:1.15;color:var(--blue)}
  .price .amount sup{font-size:30px;vertical-align:26px;margin-right:2px}
  .price .foot{position:absolute;left:0;bottom:0;width:100%;height:55px;background:var(--charcoal);color:var(--white);text-align:center;font-size:14px;line-height:1.25;padding-top:9px}
  .price .foot b{color:var(--blue-bright);font-weight:600}

  .details{left:75px;top:667px;width:300px;height:278px;background:var(--grey-panel);border-radius:0 12px 12px 12px}
  .details-text{left:115px;top:690px;width:250px;font-size:11px;line-height:1.2;color:#333}
  .details-text p{margin-bottom:14px}
  .details-text em{font-weight:700}
  .badge{width:44px;height:44px;border-radius:50%;background:var(--blue);border:3px solid var(--blue-pale)}
  .badge::after{content:"";position:absolute;left:11px;top:11px;width:16px;height:16px;border:2px solid var(--white);border-radius:50%}

  .q-title{font-weight:700;font-size:22px;color:var(--blue);background:var(--white);padding-right:6px}
  .q-box{left:416px;width:308px;border-radius:12px}
  .q-box .frame{position:absolute;left:0;top:0;right:0;bottom:0;border:1.5px solid #b9b9b9;border-radius:12px}
  .q-mark{font-weight:400;font-size:46px;line-height:1;color:#c4c4c4}
  .q-text{font-size:12px;line-height:1.22;color:var(--ink)}
  .q-text em{font-weight:700}
  .divider{left:416px;top:824px;width:308px;height:1px;background:#d3d3d3}

  .costs{left:57px;top:969px;width:668px;height:127px;border-radius:10px;overflow:hidden;background:var(--blue-sky)}
  .costs .head{height:37px;background:var(--blue-deep);color:var(--white);text-align:center;font-weight:700;font-size:20px;line-height:37px}
  .costs table{width:100%;border-collapse:collapse;table-layout:fixed}
  .costs col.c1{width:168px}.costs col.c2{width:180px}.costs col.c3{width:170px}.costs col.c4{width:150px}
  .costs th{height:36px;background:var(--blue-bright);color:var(--white);font-weight:500;font-size:12px;line-height:1.05}
  .costs td{height:54px;vertical-align:top;padding-top:11px;text-align:center;color:var(--white);font-weight:600;font-size:12px;line-height:1.15}
  .costs .amt{color:var(--ink)}
  .costs td+td,.costs th+th{border-left:1.5px solid var(--white)}

  .contact{left:0;top:1124px;width:783px;text-align:center;font-size:20px;color:var(--grey-text);font-weight:500}
  .contact b{color:var(--ink);font-weight:700}
  .contact .sep{color:var(--blue);margin:0 6px}
  .contact .mail{display:inline-block;width:15px;height:15px;border-radius:50%;background:var(--grey-text);vertical-align:1px;margin-right:4px}
  .bottom-bar{left:0;top:1184px;width:783px;height:16px;background:var(--charcoal)}
</style>
</head>
<body>
<main class="flyer">

  <svg class="hero-art" width="783" height="438" viewBox="0 0 783 438">
    <defs>
      <linearGradient id="photoTone" x1="0" y1="0" x2="1" y2="1">
        <stop offset="0" stop-color="#0a3350"/>
        <stop offset=".55" stop-color="#0677BA"/>
        <stop offset="1" stop-color="#07a6d9"/>
      </linearGradient>
    </defs>
    <rect width="783" height="438" fill="#fff"/>
    <rect y="292" width="783" height="146" fill="var(--charcoal)"/>
    <polygon points="410,0 442,0 602,438 570,438" fill="var(--charcoal)"/>
    <polygon points="448,0 488,0 648,438 608,438" fill="var(--blue-bright)"/>
    <polygon role="img" aria-label="Photo of a cheerful man in a white shirt celebrating among falling banknotes" points="496,0 783,0 783,438 656,438" fill="url(#photoTone)"/>
  </svg>

  <div class="abs brand">LedgerVale Corp.</div>

  <h1 class="abs headline">
    <div class="relax">Relax</div>
    <div class="sub">We’ve Got Your</div>
    <div class="covered">Taxes Covered!</div>
  </h1>

  <p class="abs intro">Our tax preparers have over 20 years experience and worked both in public accounting firms as well as specialized tax. Our tax services are virtual, so you don’t have to take the time for a personal visit. We take care of everything and can access all your tax slips from the revenue portal directly into our tax software. All signing is done via SignFlow.</p>
  <div class="abs esign">SignFlow</div>

  <section class="abs light-band"></section>
  <div class="abs portal-icon"></div>
  <p class="abs portal-text">You can fill and submit the appropriate forms, along with all your other documents, in our secure client portal. It’s important that we understand your situation and any changes in your situation from the past year.</p>
  <div class="abs discuss">
    <svg width="22" height="22" viewBox="0 0 22 22"><rect x="6" y="1" width="14" height="17" rx="2" fill="none" stroke="#fff" stroke-width="1.6"/><circle cx="6" cy="15" r="5" fill="var(--blue)" stroke="#fff" stroke-width="1.6"/><line x1="3.5" y1="17.5" x2="8.5" y2="12.5" stroke="#fff" stroke-width="1.4"/></svg>
    If you have a complex tax situation and would like to discuss it
  </div>
  <div class="abs laptop">
    <div class="screen">we can meet in<br>virtually over<br>MeetLine or TeamRoom
      <div class="dots"><i></i><i></i></div>
    </div>
    <div class="base"></div>
  </div>

  <div class="abs price">
    <div class="title">PERSONAL TAX RETURN</div>
    <div class="amount"><sup>$</sup>100.00</div>
    <div class="foot">Add a business or rental schedule<br><b>$125</b> per business or rental property.</div>
  </div>

  <div class="abs details"></div>
  <div class="abs badge" style="left:53px;top:695px"></div>
  <div class="abs badge" style="left:53px;top:764px"></div>
  <div class="abs badge" style="left:53px;top:839px"></div>
  <div class="abs details-text">
    <p>More complex tax returns will be assessed based on the complexity of the return and you will be advised before we start.</p>
    <p>Did you fall behind in filing your income tax save 20% when you file 3 or more years with us. We can do back to 2012 for filing of tax returns.</p>
    <p style="margin-bottom:8px">If you expect a refund, the earlier you file the sooner you will receive your refund.  Our average turn around time prior to April is a couple of days.</p>
    <p>today so you can start to <em>breathe easy.</em></p>
  </div>

  <div class="abs q-box" style="top:692px;height:104px"><div class="frame"></div></div>
  <h2 class="abs q-title" style="left:416px;top:676px">How will you feel?</h2>
  <div class="abs q-mark" style="left:420px;top:718px">?</div>
  <p class="abs q-text" style="left:457px;top:722px;width:250px">Calm, relaxed, and able to make good business decisions. And you’ll have more time to work on your business. In short, you’ll be able to <em>breathe easy.</em></p>

  <div class="abs divider"></div>

  <div class="abs q-box" style="top:868px;height:74px"><div class="frame"></div></div>
  <h2 class="abs q-title" style="left:416px;top:852px">Sound too good to be true?</h2>
  <div class="abs q-mark" style="left:420px;top:892px">?</div>
  <p class="abs q-text" style="left:457px;top:897px;width:230px">That’s exactly how our clients feel once all their bookkeeping stresses are gone.</p>

  <section class="abs costs">
    <div class="head">Bookkeeping &amp; Accounting Costs</div>
    <table>
      <colgroup><col class="c1"><col class="c2"><col class="c3"><col class="c4"></colgroup>
      <tr><th>DIY</th><th>Part-Time Bookkeeper</th><th>Full-Time Bookkeeper</th><th>Full Outsourced<br>Accounting Team</th></tr>
      <tr><td>No added<br>financial cost</td><td><span class="amt">$3,500-4,500/</span><br>month + benefits</td><td><span class="amt">$4,800-5,500/</span><br>month + benefits</td><td><span class="amt">$5,000+</span></td></tr>
    </table>
  </section>

  <p class="abs contact">CONTACT US TODAY! <b>014.555.0199</b><span class="sep">|</span><span class="mail"></span><b>hello@ledgervale.ca</b></p>
  <div class="abs bottom-bar"></div>
</main>
</body>
</html>
```